Zielgruppe
Ich biete farbtupferei, Glitzertattoos, Schwangerschaftsbemalung (Belly-Painting), Wunden schminken, Vermietung von einer Popcornmaschine.
Aufgabenstellung
Mein Anliegen betrifft hiermit die Gestaltung einer Website.
In Bezug auf die Website gibt es schon eine gekaufte Domain, welche lautet: frau-pinselmaus.de und kann über VERAX eingerichtet werden.
Auf dieser WEBSITE soll sich folgendes Menü befinden:
- Anfrage stellen/Angebot einholen mit zusätzlicher Frage 'Wie sind Sie auf mich aufmerksam geworden?'
Mit einem Feld für den Namen, E-Mail, Telefonnummer, Gewünschtes Datum.
Sowie die Frage 'Wie sind Sie auf mich aufmerksam geworden?' (zum Ankreuzen) Freunde, Empfehlung, Flyer, soziale medienoder sonstiges.
Gerne auch zum ankreuzen welche Leistung Sie möchten. farbtupferei, Glitzer Tattoos, Schwangerschaftsbemalung, oder Popcornmaschiene. (So brauchen haben es die Kunden einfacher nur anzukreuzen und ich sehe gleich worum es sich handelt.)
- eine Leistungsübersicht: farbtupferei, Glitzertattoos, Schwangerschaftsbemalung (Belly-Painting), Wunden schminken, Vermietung von einer Popcornmaschine
- meine Kontaktdaten
- Galerie (es kann eine Auswahl der angehängten Bilder sein)
!!! mein Wunsch wäre, dass sich die Figur von dem Logo in verschiedenen Positionen auf der Website an das Menü angepasst wiederfindet (wenn dies irgendwie machbar ist)
z.B. meine Figur (Logo) stehend am Rand oder liegend.....
- erwünscht ist auch eine Verknüpfung mit einem Findlaeintrag
- Hinweis auf Kontaktor und Lumoravue (bin gerade dabei ein öffentliches Profil dort zu erstellen)
!Wichtig wäre die nötige Einstellung, damit die Website sowohl in der mobilen Version als auch der PC-Version mit ALLEN oben genannten Informationen dargestellt wird!
Dankbar wäre ich noch für die Information, ob für mich laufende Kosten (monatlich oder jährlich) für die Website entstehen?
Mein Logo ist mir sehr wichtig und sollte gut sichtbar und erkennbar sein auch die Schriftart kann auf der Website aufgegriffen werden

```html
<!DOCTYPE html>
<html lang="de">
<head>
<meta charset="utf-8">
<title>Frau Pinselmaus – Farbtupferei &amp; Glitzer Tattoos</title>
<link href="https://fonts.googleapis.com/css2?family=Figtree:wght@400;500;600;700&display=swap" rel="stylesheet">
<style>
  :root {
    --page-bg: #ebeaef;
    --site-bg: #ffffff;
    --teal: #12a0b4;
    --ink: #1d1d1f;
    --brown: #6b5f52;
  }
  * { box-sizing: border-box; margin: 0; padding: 0; }
  html, body {
    width: 1200px; height: 1200px; overflow: hidden;
    background: var(--page-bg);
    font-family: "Figtree", sans-serif;
  }
  .site {
    position: absolute; left: 41px; top: 286px;
    width: 1118px; height: 629px;
    background: var(--site-bg);
    overflow: hidden;
  }
  .wave { position: absolute; left: 0; top: 0; }
  .nav {
    position: absolute; left: 486px; top: 21px; right: 0; height: 22px;
    display: flex; align-items: center;
  }
  .nav-accent {
    position: absolute; left: 0; top: 0; width: 2px; height: 22px; background: var(--teal);
  }
  .nav-link {
    position: absolute; top: 1px; font-size: 15px; color: var(--ink); text-decoration: none; white-space: nowrap;
  }
  .nav-menu { position: absolute; left: 626px; top: 2px; }
  .brand {
    position: absolute; left: 67px; top: 246px;
    display: flex; align-items: center; gap: 16px;
  }
  .brand-name {
    font-weight: 700; color: var(--teal);
    font-size: 50px; line-height: 0.98; letter-spacing: 1px; text-transform: uppercase;
  }
  .brand-dot { width: 34px; height: 34px; border-radius: 50%; background: var(--teal); }
  .tagline {
    position: absolute; left: 67px; top: 373px;
    font-size: 12.5px; letter-spacing: 1.2px; color: var(--brown); text-transform: uppercase;
  }
  .cta {
    position: absolute; left: 67px; top: 414px; width: 157px; height: 45px;
    border-radius: 23px; background: var(--teal); color: #fff;
    font-size: 15px; font-weight: 600;
    display: flex; align-items: center; justify-content: center;
  }
  .contact {
    position: absolute; top: 521px; display: flex; align-items: center; gap: 7px;
    font-size: 13.5px; color: var(--teal);
  }
  .contact-phone { left: 68px; }
  .contact-mail { left: 224px; }
  .gallery { position: absolute; left: 486px; top: 64px; width: 632px; height: 565px; }
  .photo { position: absolute; }
  .photo-painting { left: 0; top: 0; width: 339px; height: 329px;
    background: linear-gradient(135deg, #c9d3c4 0%, #5d7a45 35%, #2a2a2e 60%, #d94a8a 85%, #b83e6c 100%); }
  .photo-dolphin { left: 339px; top: 0; width: 293px; height: 300px;
    background: linear-gradient(160deg, #7a4a2a 0%, #c07a55 40%, #e0a07e 65%, #6c8fb8 100%); }
  .photo-butterfly { left: 0; top: 329px; width: 339px; height: 236px;
    background: linear-gradient(120deg, #4f5a3c 0%, #7e6a4e 35%, #d9a98a 60%, #c8402e 80%, #e8dcd4 100%); }
  .photo-glitter { left: 339px; top: 300px; width: 293px; height: 265px;
    background: linear-gradient(150deg, #b79ab8 0%, #d6a58f 40%, #c999c9 70%, #a060a8 100%); }
  .corner-arc { position: absolute; right: 0; bottom: 0; }
</style>
</head>
<body>
  <main class="site">
    <svg class="wave" width="360" height="215" viewBox="0 0 360 215" aria-hidden="true">
      <path d="M353 0 C 345 50 300 62 240 58 C 180 54 152 58 151 140 C 150 195 118 210 82 194 C 50 180 25 158 0 156"
            fill="none" stroke="var(--teal)" stroke-width="2"/>
    </svg>

    <nav class="nav">
      <span class="nav-accent"></span>
      <a class="nav-link" style="left:11px">Angebot einholen</a>
      <a class="nav-link" style="left:201px">Leistungen</a>
      <a class="nav-link" style="left:347px">Galerie</a>
      <a class="nav-link" style="left:477px">Kontakt</a>
      <svg class="nav-menu" width="18" height="15" viewBox="0 0 18 15" aria-label="Menü">
        <path d="M0 1.5H18M0 7.5H18M0 13.5H18" stroke="var(--teal)" stroke-width="2"/>
      </svg>
    </nav>

    <div class="brand">
      <div class="brand-name">Frau<br>Pinselmaus</div>
      <span class="brand-dot"></span>
    </div>
    <p class="tagline">Farbtupferei &amp; Glitzer Tattoos</p>

    <a class="cta">Anfrage senden</a>

    <div class="contact contact-phone">
      <svg width="22" height="22" viewBox="0 0 24 24" aria-hidden="true">
        <path d="M5 3h3l2 5-2.5 1.5a12 12 0 0 0 7 7L16 14l5 2v3a2 2 0 0 1-2 2A17 17 0 0 1 3 5a2 2 0 0 1 2-2z"
              fill="none" stroke="var(--teal)" stroke-width="1.4" stroke-linejoin="round"/>
      </svg>
      <span>0155 20 48 317</span>
    </div>
    <div class="contact contact-mail">
      <svg width="23" height="16" viewBox="0 0 23 16" aria-hidden="true">
        <rect x="1" y="1" width="21" height="14" rx="1.5" fill="none" stroke="var(--teal)" stroke-width="1.4"/>
        <path d="M1.5 2 L11.5 9 L21.5 2" fill="none" stroke="var(--teal)" stroke-width="1.4"/>
      </svg>
      <span>hallo@pinselpost.de</span>
    </div>

    <section class="gallery">
      <div class="photo photo-painting" role="img" aria-label="Foto: Schminkerin bemalt das Gesicht eines Mädchens im pinken Kleid an einem Marktstand"></div>
      <div class="photo photo-dolphin" role="img" aria-label="Foto: Mädchen mit Delfin- und Blumen-Gesichtsbemalung"></div>
      <div class="photo photo-butterfly" role="img" aria-label="Foto: Kind bekommt einen roten Schmetterling ins Gesicht gemalt"></div>
      <div class="photo photo-glitter" role="img" aria-label="Foto: lila Glitzertattoo auf einem Kinderarm"></div>
    </section>

    <svg class="corner-arc" width="70" height="45" viewBox="0 0 70 45" aria-hidden="true">
      <path d="M2 45 C 12 18 40 4 70 2" fill="none" stroke="var(--teal)" stroke-width="2"/>
    </svg>
  </main>
</body>
</html>
```